New business card/stationary for a consulting company

I am looking for a clean and very professional looking business card for my consulting company as well as corresponding stationary. I am uploading our logo. I like simple and powerful for the feel. No graphics but I am open on everything else. Below is my contact information but would like the final to be in a version I can add my employees information into and print. Thank you.

Daniel Whitcombe
dan@ferncliffadvisory.com
2870 North 9th Avenue, Summit Floor, Elm Ridge, Illinois 60531
www.ferncliffadvisory.com

Industry/Entity Type

Consulting

Contact Information for Business Card

Daniel Whitcombe
dan@ferncliffadvisory.com
www.ferncliffadvisory.com

Font styles to use
Serif
Sans Serif

Requirements
Must have
• Our logo and the business card details.
Nice to have
• our website www.ferncliffadvisory.com

```html
<!DOCTYPE html>
<html lang="en">
<head>
<meta charset="utf-8">
<title>Ferncliff Advisory — Business Card</title>
<link rel="stylesheet" href="https://fonts.googleapis.com/css2?family=Montserrat:wght@300;400;500;700&display=swap">
<style>
  :root {
    --navy: #1d1a72;
    --white: #ffffff;
    --stage: #e4e5e7;
    --rule: rgba(255,255,255,0.75);
  }
  * { box-sizing: border-box; margin: 0; padding: 0; }
  html, body { width: 1200px; height: 1022px; overflow: hidden; }
  body {
    background: var(--stage);
    font-family: 'Montserrat', sans-serif;
    position: relative;
  }
  .card {
    position: absolute;
    width: 580px;
    height: 330px;
    overflow: hidden;
    box-shadow: 0 6px 18px rgba(0,0,0,0.18);
  }

  /* Front */
  .card-front {
    left: 70px; top: 110px;
    background: var(--navy);
    color: var(--white);
  }
  .front-brand {
    position: absolute;
    left: 0; right: 0; top: 112px;
    display: flex; align-items: center; justify-content: center; gap: 16px;
  }
  .brand-square { width: 26px; height: 26px; background: var(--white); }
  .front-brand .brand-name {
    font-weight: 300; font-size: 30px; letter-spacing: 1.5px; text-transform: uppercase;
  }
  .front-rule {
    position: absolute; left: 64px; right: 64px; top: 170px;
    height: 1.5px; background: var(--rule);
  }
  .front-web {
    position: absolute; left: 40px; right: 40px; top: 214px;
    display: flex; align-items: center; gap: 14px;
    font-size: 12px; font-weight: 500; letter-spacing: 0.3px;
  }
  .front-web .line { flex: 1; height: 1.5px; background: var(--rule); }

  /* Back */
  .card-back {
    left: 550px; top: 570px;
    background: var(--white);
  }
  .back-brand {
    position: absolute; left: 0; right: 0; top: 62px;
    display: flex; align-items: center; justify-content: center; gap: 12px;
    color: var(--navy);
  }
  .back-brand .brand-square { width: 20px; height: 20px; background: var(--navy); }
  .back-brand .brand-name {
    font-weight: 400; font-size: 24px; letter-spacing: 1.2px; text-transform: uppercase;
  }
  .back-band {
    position: absolute; left: 0; right: 0; top: 150px; bottom: 0;
    background: var(--navy); color: var(--white);
  }
  .band-notch { position: absolute; left: 96px; top: -1px; }
  .person {
    position: absolute; left: 44px; top: 40px;
  }
  .person-name { font-weight: 700; font-size: 19px; margin-bottom: 10px; }
  .person-title { font-weight: 700; font-size: 12.5px; margin-bottom: 10px; }
  .person-address { font-weight: 300; font-size: 12.5px; line-height: 1.9; }
  .band-divider {
    position: absolute; left: 338px; top: 22px; bottom: 36px;
    width: 1.5px; background: var(--rule);
  }
  .contacts {
    position: absolute; left: 362px; top: 24px;
    list-style: none;
  }
  .contacts li {
    display: flex; align-items: center; gap: 10px;
    font-size: 12.5px; font-weight: 300; line-height: 25px;
  }
  .contacts svg { width: 12px; height: 12px; fill: var(--white); flex: none; }
</style>
</head>
<body>

  <section class="card card-front" aria-label="Business card front">
    <div class="front-brand">
      <span class="brand-square"></span>
      <span class="brand-name">Ferncliff Advisory</span>
    </div>
    <div class="front-rule"></div>
    <div class="front-web">
      <span class="line"></span>
      <span class="web-address">www.ferncliffadvisory.com</span>
      <span class="line"></span>
    </div>
  </section>

  <section class="card card-back" aria-label="Business card back">
    <div class="back-brand">
      <span class="brand-square"></span>
      <span class="brand-name">Ferncliff Advisory</span>
    </div>
    <div class="back-band">
      <svg class="band-notch" width="22" height="12" viewBox="0 0 22 12"><polygon points="0,0 22,0 11,11" fill="#ffffff"/></svg>
      <div class="person">
        <p class="person-name">Daniel Whitcombe</p>
        <p class="person-title">Founder / Principal</p>
        <p class="person-address">2870 North 9th Avenue, Summit Floor,<br>Elm Ridge, Illinois 60531</p>
      </div>
      <div class="band-divider"></div>
      <ul class="contacts">
        <li><svg viewBox="0 0 24 24"><path d="M6.6 10.8a15.1 15.1 0 0 0 6.6 6.6l2.2-2.2c.3-.3.7-.4 1-.2 1.1.4 2.3.6 3.6.6.6 0 1 .4 1 1V20c0 .6-.4 1-1 1A17 17 0 0 1 3 4c0-.6.4-1 1-1h3.5c.6 0 1 .4 1 1 0 1.3.2 2.5.6 3.6.1.3 0 .7-.2 1z"/></svg>(855) 310 27846</li>
        <li><svg viewBox="0 0 24 24"><path d="M7 1h10a2 2 0 0 1 2 2v18a2 2 0 0 1-2 2H7a2 2 0 0 1-2-2V3a2 2 0 0 1 2-2zm0 3v14h10V4zm5 15.5a1.2 1.2 0 1 0 0 2.4 1.2 1.2 0 0 0 0-2.4z"/></svg>+918012734560</li>
        <li><svg viewBox="0 0 24 24"><path d="M2 5h20v14H2zm2 2v.4l8 5.2 8-5.2V7zm0 2.8V17h16V9.8l-8 5.2z"/></svg>dan@ferncliffadvisory.com</li>
        <li><svg viewBox="0 0 24 24"><path d="M12 2a10 10 0 1 0 0 20 10 10 0 0 0 0-20zm6.9 6h-2.9a15 15 0 0 0-1.3-3.6A8 8 0 0 1 18.9 8zM12 4c.8 1.2 1.5 2.5 1.9 4h-3.8c.4-1.5 1.1-2.8 1.9-4zM4.3 14a8 8 0 0 1 0-4h3.3a16 16 0 0 0 0 4zm.8 2h2.9c.3 1.3.8 2.5 1.3 3.6A8 8 0 0 1 5.1 16zM8 8H5.1a8 8 0 0 1 4.2-3.6C8.8 5.5 8.3 6.7 8 8zm4 12c-.8-1.2-1.5-2.5-1.9-4h3.8c-.4 1.5-1.1 2.8-1.9 4zm2.3-6H9.7a14 14 0 0 1 0-4h4.6a14 14 0 0 1 0 4zm.4 5.6c.5-1.1 1-2.3 1.3-3.6h2.9a8 8 0 0 1-4.2 3.6zm1.7-5.6a16 16 0 0 0 0-4h3.3a8 8 0 0 1 0 4z"/></svg>www.ferncliffadvisory.com</li>
      </ul>
    </div>
  </section>

</body>
</html>
```